Business Card for Polygraph business in Africa

Business Card . Polygraph Examiner based in Tanzania, East Africa.
Business Card will be used to disseminate contact information to potential clients.
It should convey that I am a professional specifically in the polygraph field and perform my work with integrity.

I have attached the business card that I'm currently using, which I threw together myself initially. It's not professional enough.

Target Market(s)

Banks, Accounting Firms, Government Ministries, Gas, Oil, & Gemstone Mining Concerns, Wildlife Conservation NGOs, International companies located in East Africa.

Industry/Entity Type

Business

Contact Information for Business Card

Veritrace Kilonga
Miriam Holloway
PO Box 48317
Arusha, Tanzania
+255 612 839 274
miriamholloway@postvale.example

Colors
00a990
f37122
faa54b

Requirements
Must have
• - Veritrace Kilonga (with the word "Polygraph" being more prominent than the word "Tanzania")
• - Forensic Examinations
• - Employment Screening
• - Should contain a logo of the Continental Truthline Society (of which I'm a member)
• - I would like an accent design (such as the polygraph "squiggles" of a cardio tracing or such as that)
• - My contact information (less prominent, but large enough to read legibly). I would also consider putting the contact information on the second side of the card.
Nice to have
• My color suggestions are changeable.
Should not have
• Anything "cutesy" or "cartoonish"

```html
<!DOCTYPE html>
<html lang="en">
<head>
<meta charset="utf-8">
<title>Veritrace Kilonga – Business Card</title>
<link rel="stylesheet" href="https://fonts.googleapis.com/css2?family=Roboto:wght@400;500;700&display=swap">
<style>
  :root {
    --brand-blue: #0d4a9e;
    --badge-violet: #3a3596;
    --ink-grey: #555a60;
    --rule-grey: #9a9ea3;
    --card-white: #fbfbfb;
    --edge-grey: #d3d5d8;
    --page-bg: #e9eaec;
  }
  * { box-sizing: border-box; margin: 0; padding: 0; }
  html, body { width: 1200px; height: 900px; overflow: hidden; }
  body {
    background: var(--page-bg);
    font-family: "Roboto", Arial, sans-serif;
    position: relative;
  }
  .card {
    position: absolute;
    left: 320px;
    width: 560px;
    height: 320px;
    border-radius: 18px;
    overflow: hidden;
    box-shadow: 0 6px 18px rgba(0,0,0,0.18);
  }

  /* Back side */
  .card-back { top: 60px; background: var(--brand-blue); color: #fff; }
  .back-mark {
    position: absolute; left: 0; right: 0; top: 112px;
    display: flex; align-items: center; justify-content: center; gap: 14px;
  }
  .back-mark .dot {
    width: 34px; height: 34px; border: 3px solid #fff; border-radius: 50%;
  }
  .back-mark .name { font-size: 32px; font-weight: 700; letter-spacing: 0.5px; }
  .services {
    position: absolute; left: 40px; bottom: 36px;
    font-size: 14px; letter-spacing: 0.3px;
  }
  .services .sep { display: inline-block; width: 6px; height: 6px; background: #fff; border-radius: 50%; margin: 0 10px; vertical-align: middle; }

  /* Front side */
  .card-front { top: 470px; background: var(--card-white); }
  .member-badge {
    position: absolute; left: 30px; top: 24px;
    width: 62px; height: 62px; border-radius: 50%;
    border: 4px solid var(--badge-violet);
    background: #e8e7f3;
  }
  .holder { position: absolute; left: 40px; top: 104px; width: 250px; }
  .holder-name { color: var(--brand-blue); font-size: 20px; font-weight: 700; letter-spacing: 0.2px; line-height: 24px; }
  .holder-company { color: var(--ink-grey); font-size: 14px; line-height: 18px; margin-top: 2px; letter-spacing: 0.4px; }
  .holder-rule { height: 1px; background: var(--rule-grey); margin: 8px 0; width: 190px; }
  .contact-list { list-style: none; }
  .contact-list li { display: flex; align-items: center; gap: 8px; font-size: 13px; color: var(--ink-grey); line-height: 20px; white-space: nowrap; }
  .contact-list svg { width: 11px; height: 11px; fill: var(--brand-blue); flex: none; }

  .front-mark {
    position: absolute; right: 36px; top: 112px;
    display: flex; align-items: center; gap: 12px;
  }
  .front-mark .dot { width: 34px; height: 34px; border: 3px solid var(--brand-blue); border-radius: 50%; }
  .front-mark .name { color: var(--brand-blue); font-size: 28px; font-weight: 700; }

  .divider {
    position: absolute; left: 300px; right: 36px; top: 170px;
    height: 1px; background: var(--rule-grey);
  }
  .address {
    position: absolute; right: 40px; bottom: 26px;
    text-align: right; color: var(--ink-grey); font-size: 14px; line-height: 19px;
    font-style: normal;
  }
  .edge-band {
    position: absolute; left: 0; bottom: 0; height: 8px; width: 330px;
    background: var(--brand-blue);
  }
  .edge-band-grey {
    position: absolute; left: 330px; bottom: 0; height: 8px; right: 0;
    background: var(--edge-grey);
  }
</style>
</head>
<body>

  <section class="card card-back" aria-label="Card back">
    <div class="back-mark">
      <span class="dot"></span>
      <span class="name">Veritrace Kilonga</span>
    </div>
    <p class="services">Forensic Examinations<span class="sep"></span>Employment Screening</p>
  </section>

  <section class="card card-front" aria-label="Card front">
    <div class="member-badge" role="img" aria-label="Continental Truthline Society membership badge"></div>

    <div class="holder">
      <h1 class="holder-name">MIRIAM HOLLOWAY</h1>
      <p class="holder-company">VERITRACE KILONGA</p>
      <div class="holder-rule"></div>
      <ul class="contact-list">
        <li>
          <svg viewBox="0 0 24 24"><path d="M6.6 10.8c1.4 2.8 3.8 5.1 6.6 6.6l2.2-2.2c.3-.3.7-.4 1-.2 1.1.4 2.3.6 3.6.6.6 0 1 .4 1 1V20c0 .6-.4 1-1 1C10.6 21 3 13.4 3 4c0-.6.4-1 1-1h3.5c.6 0 1 .4 1 1 0 1.3.2 2.5.6 3.6.1.3 0 .7-.2 1L6.6 10.8z"/></svg>
          +255 612 839 274
        </li>
        <li>
          <svg viewBox="0 0 24 24"><path d="M2 5h20v14H2z M2 5l10 8 10-8" /></svg>
          miriamholloway@postvale.example
        </li>
        <li>
          <svg viewBox="0 0 24 24"><circle cx="12" cy="12" r="10"/></svg>
          www.miriamholloway.example
        </li>
      </ul>
    </div>

    <div class="front-mark">
      <span class="dot"></span>
      <span class="name">Veritrace Kilonga</span>
    </div>

    <div class="divider"></div>

    <address class="address">
      PO Box 48317<br>Arusha, Tanzania
    </address>

    <div class="edge-band"></div>
    <div class="edge-band-grey"></div>
  </section>

</body>
</html>
```